Children’s entertainer/balloon artist Website Home Page and custom landing page

I need a home page design for the home page of a children and family entertainer/balloon twister’s website. I also need a custom landing page for family theatre shows performed by the same entertainer.
It will be a Wordpress website and I need the final artwork in a layer Photoshop file with all the layers clearly named and labeled.

Target Market(s)

The site visitors are mainly mums, aged between early 20’s and late 30’s. Other visitors will included companies for Christmas functions, and event organisers for corporate functions.

Industry/Entity Type

Entertainment

Number of Pages Required

2 page

Font styles to use
Sans Serif

Colors
34a6d7
f37122

Requirements
Must have
• Layout
• I have included a wireframe for the home page layout and the custom landing page for your reference. This is a guide only and I welcome your interpretation with the rough layout provided.
• This website needs to look good on all devices as it will be fully responsive.
• It needs to include a footer area on the page, that has social media and a call to action area included.
• Colours
• The main colours for the site is:
• orange (call to action colour)
• ff6800
• blue/turquoise
• 42abc3
• Pictures
• I have included images of the entertainer/balloon artist for you to use/take inspiration from.
• These images will be included on the website. I want to show lots of people having fun.
• I would like to have elements of the logo used in isolation across the website
• i.e. the octopus figure to be included in the footer or the bird element to be included in the testimonial slider etc.
• Elements to include
• Note: use the images of the entertainer in the boxes on the home page (balloon shows, balloon twisting, balloon workshops, theatre shows (the three little balloon pigs on his head)
Nice to have
Should not have
• Element to avoid
• Stock imagery of balloon sculptures - use images provided.

```html
<!DOCTYPE html>
<html lang="en">
<head>
<meta charset="utf-8">
<title>Toby Marlowe – Kids Entertainer and Balloon Artist</title>
<link href="https://fonts.googleapis.com/css2?family=Open+Sans:wght@400;600;700;800&family=Luckiest+Guy&display=swap" rel="stylesheet">
<style>
:root{
  --sky-top:#5fb8e6;
  --sky-bottom:#cfeaf8;
  --page:#f4f6f7;
  --teal:#42abc3;
  --teal-dark:#2f8fa6;
  --blue:#34a6d7;
  --orange:#ff6800;
  --orange-soft:#f37122;
  --red:#d8232a;
  --red-dark:#b3161d;
  --yellow:#f7c51e;
  --navy:#123a63;
  --navy-dark:#0c2a4a;
  --text:#444;
  --muted:#888;
  --white:#fff;
}
*{box-sizing:border-box;margin:0;padding:0}
html,body{width:710px;height:1200px;overflow:hidden}
body{font-family:"Open Sans",Arial,sans-serif;color:var(--text);background:linear-gradient(var(--sky-top) 0,var(--sky-bottom) 380px,var(--sky-bottom) 100%);position:relative}
.canvas{position:relative;width:710px;height:1200px}

/* header */
.brand{position:absolute;left:14px;top:8px;width:180px;height:80px;display:flex;align-items:center;gap:8px}
.brand-dot{width:26px;height:26px;border-radius:50%;background:var(--orange)}
.brand-name{font-weight:800;font-size:22px;color:var(--navy)}
.tagline{position:absolute;left:208px;top:28px;font-size:15px;font-weight:600;color:var(--white)}
.booking{position:absolute;left:452px;top:26px;display:flex;align-items:center;gap:6px;color:var(--white);font-weight:700;font-size:14px}
.nav{position:absolute;left:208px;top:62px;width:444px;height:24px;background:var(--red);border-radius:3px;display:flex;align-items:stretch;padding-left:4px}
.nav a{font-size:7.5px;font-weight:700;color:var(--white);text-decoration:none;text-transform:uppercase;display:flex;align-items:center;padding:0 12px;border-right:1px solid var(--red-dark)}
.nav a.is-active{background:var(--yellow);color:var(--red-dark);margin:3px 0;border-radius:2px}

.page{position:absolute;left:44px;top:92px;width:622px;height:910px;background:var(--page)}

/* hero */
.hero{position:absolute;left:59px;top:98px;width:593px;height:258px;border-radius:4px;overflow:hidden;background:linear-gradient(120deg,#1d6fae,#52b6e8 55%,#2a84c4)}
.hero-photo{position:absolute;right:0;top:0;width:330px;height:258px;background:radial-gradient(circle at 60% 50%,#6bc4ee,#2c8ccc 70%)}
.hero-title{position:absolute;left:24px;top:128px;font-family:"Luckiest Guy","Open Sans",sans-serif;color:var(--white);font-size:25px;line-height:1.18;letter-spacing:.5px;text-transform:uppercase}
.hero-dots{position:absolute;left:50%;bottom:8px;transform:translateX(-50%);display:flex;gap:5px}
.hero-dots span{width:6px;height:6px;border-radius:50%;background:rgba(255,255,255,.6)}
.hero-dots span:first-child{background:var(--white)}

/* testimonials */
.testimonials{position:absolute;left:59px;top:374px;width:443px;height:119px;background:var(--teal);border-radius:5px;padding:14px 16px 0 100px;color:var(--white)}
.testimonial-photo{position:absolute;left:22px;top:22px;width:64px;height:64px;border-radius:50%;background:linear-gradient(#d8c4b4,#9e8576);border:3px solid var(--white)}
.testimonials h3{font-size:13px;font-weight:700;margin-bottom:6px}
.testimonials p{font-size:7px;line-height:1.5}
.testimonials cite{display:block;font-size:7px;margin-top:4px;font-style:italic}
.promo{position:absolute;left:516px;top:374px;width:136px;height:119px;border-radius:5px;background:linear-gradient(#2b8fd0,#1a5f9e);padding:16px 12px;color:var(--white)}
.promo strong{display:block;font-size:15px;font-weight:800;line-height:1.1;text-transform:uppercase}
.promo .btn{position:absolute;left:12px;bottom:14px}

/* about */
.about-title{position:absolute;left:59px;top:513px;font-size:15px;font-weight:700;color:var(--orange-soft)}
.about-photo{position:absolute;left:59px;top:540px;width:100px;height:90px;background:linear-gradient(#f4d5dd,#ec9fb3)}
.about-text{position:absolute;left:168px;top:540px;width:334px;font-size:6.5px;line-height:1.6;color:var(--muted)}
.about-text p+p{margin-top:6px}
.about .btn{position:absolute;left:168px;top:602px}

.photo-feed{position:absolute;left:516px;top:505px;width:136px}
.photo-feed h4{font-size:14px;font-weight:600;color:var(--text);margin-bottom:6px}
.feed-grid{display:grid;grid-template-columns:repeat(3,40px);gap:4px}
.feed-grid span{width:40px;height:40px;background:linear-gradient(#8fcbe8,#3c89b8)}
.feed-grid span:nth-child(2n){background:linear-gradient(#f7c36a,#e2733b)}
.feed-grid span:nth-child(3n){background:linear-gradient(#c9d79b,#6c9a4c)}
.feed-foot{margin-top:5px;height:16px;border:1px solid #ccc;font-size:7px;display:flex;align-items:center;justify-content:space-between;padding:0 5px;background:var(--white)}

/* service cards */
.services{position:absolute;left:59px;top:722px;width:593px;display:flex;gap:19px}
.card{width:134px;height:262px;border-radius:6px;padding:14px 10px;color:var(--white);text-align:center;position:relative}
.card--red{background:linear-gradient(#ef3f3a,#c8191f)}
.card--orange{background:linear-gradient(#ffbe1a,#f59b12)}
.card--blue{background:linear-gradient(#38b3ea,#1b7fc4)}
.card--teal{background:linear-gradient(#3dbfae,#1c8f83)}
.card h3{font-size:18px;font-weight:800;line-height:1.1}
.card-photo{width:100px;height:92px;margin:12px auto 10px;border-radius:6px;background:rgba(255,255,255,.28)}
.card p{font-size:7px;line-height:1.5}
.card .btn{position:absolute;left:17px;right:17px;bottom:16px;justify-content:center}

.btn{display:inline-flex;align-items:center;height:18px;padding:0 12px;background:var(--red);border-radius:3px;color:var(--white);font-size:7.5px;font-weight:700;text-decoration:none;box-shadow:0 1px 0 var(--red-dark)}

/* footer */
.footer{position:absolute;left:0;top:1020px;width:710px;height:166px;background:var(--navy);color:#c9d6e3}
.footer-cols{position:absolute;left:59px;top:22px;width:593px;display:flex;gap:24px}
.footer-col h5{font-size:9px;color:var(--white);font-weight:700;margin-bottom:8px}
.footer-col li{list-style:none;font-size:6.5px;line-height:1.75}
.footer-col p{font-size:6.5px;line-height:1.6}
.col-welcome{width:90px}.col-contact{width:140px}.col-news{width:160px}.col-social{width:130px}
.field{display:flex;margin-top:8px}
.field span{width:110px;height:16px;background:var(--white);font-size:6px;color:#999;padding:4px 5px}
.field b{height:16px;padding:0 8px;background:var(--orange);color:var(--white);font-size:6.5px;display:flex;align-items:center}
.social{display:flex;gap:5px;margin-top:8px}
.social span{width:16px;height:16px;border-radius:50%;background:#c9d6e3}
.contact-line{display:flex;align-items:center;gap:4px}
.copyright{position:absolute;left:0;top:1186px;width:710px;height:14px;background:var(--navy-dark);color:#9fb2c6;font-size:6px;text-align:center;line-height:14px}
</style>
</head>
<body>
<div class="canvas">

  <header class="site-header">
    <div class="brand"><span class="brand-dot"></span><span class="brand-name">Toby Twists</span></div>
    <p class="tagline">kids entertainer and balloon artist</p>
    <div class="booking">
      <svg width="14" height="14" viewBox="0 0 24 24" aria-hidden="true"><path fill="#fff" d="M6.6 10.8a15 15 0 0 0 6.6 6.6l2.2-2.2c.3-.3.7-.4 1-.2 1.1.4 2.3.6 3.6.6.6 0 1 .4 1 1V20c0 .6-.4 1-1 1A17 17 0 0 1 3 4c0-.6.4-1 1-1h3.5c.6 0 1 .4 1 1 0 1.3.2 2.5.6 3.6.1.3 0 .7-.2 1z"/></svg>
      <span>Book Now : (0123) 456 789</span>
    </div>
    <nav class="nav">
      <a href="#" class="is-active">Home</a>
      <a href="#">Balloon Shows</a>
      <a href="#">Balloon Twisting</a>
      <a href="#">Theatre</a>
      <a href="#">Reviews</a>
      <a href="#">Contact</a>
    </nav>
  </header>

  <div class="page"></div>

  <section class="hero">
    <div class="hero-photo" role="img" aria-label="Photo of the entertainer holding colourful balloon sculptures"></div>
    <h1 class="hero-title">Toby Marlowe<br>Kids Entertainer and<br>Balloon Artist</h1>
    <div class="hero-dots"><span></span><span></span><span></span></div>
  </section>

  <section class="testimonials">
    <div class="testimonial-photo" role="img" aria-label="Portrait of a happy parent"></div>
    <h3>Testimonials</h3>
    <p>Toby was a fantastic hit at my son's party. The children laughed from start to finish and every single guest went home with a balloon animal. We will certainly be booking him again for next year.</p>
    <cite>– Sarah, parent</cite>
  </section>
  <aside class="promo">
    <strong>Kids<br>Entertainer</strong>
    <a href="#" class="btn">Click here</a>
  </aside>

  <section class="about">
    <h2 class="about-title">About Toby Marlowe</h2>
    <div class="about-photo" role="img" aria-label="Photo of the entertainer wearing three balloon pigs on his head"></div>
    <div class="about-text">
      <p>A kids entertainer and balloon artist bringing fun and laughter to parties, schools, festivals and family events across the region for many years.</p>
      <p>Toby offers interactive balloon shows, balloon twisting, workshops and family theatre, each one packed with comedy, magic and colourful balloon creations for children of every age.</p>
    </div>
    <a href="#" class="btn">Read more info</a>
  </section>

  <aside class="photo-feed">
    <h4>Photo wall</h4>
    <div class="feed-grid" role="img" aria-label="Grid of party photos">
      <span></span><span></span><span></span><span></span><span></span><span></span><span></span><span></span><span></span>
    </div>
    <div class="feed-foot"><span>Follow along</span><span>Subscribe</span></div>
  </aside>

  <section class="services">
    <article class="card card--red">
      <h3>Balloon<br>shows</h3>
      <div class="card-photo" role="img" aria-label="Balloons photo"></div>
      <p>Lively comedy shows full of balloons and laughs.</p>
      <a href="#" class="btn">Click here</a>
    </article>
    <article class="card card--orange">
      <h3>Balloon<br>twisting</h3>
      <div class="card-photo" role="img" aria-label="Heart balloon sculptures photo"></div>
      <p>Amazing balloon models twisted for every guest.</p>
      <a href="#" class="btn">Click here</a>
    </article>
    <article class="card card--blue">
      <h3>Balloon<br>workshops</h3>
      <div class="card-photo" role="img" aria-label="Party balloons photo"></div>
      <p>Hands-on sessions where children make their own.</p>
      <a href="#" class="btn">Click here</a>
    </article>
    <article class="card card--teal">
      <h3>Theatre<br>shows</h3>
      <div class="card-photo" role="img" aria-label="Theatre show photo"></div>
      <p>Family theatre full of songs, stories and fun.</p>
      <a href="#" class="btn">Click here</a>
    </article>
  </section>

  <footer class="footer">
    <div class="footer-cols">
      <div class="footer-col col-welcome">
        <h5>Welcome</h5>
        <ul><li>Home</li><li>Balloon Shows</li><li>Balloon Twisting</li><li>Theatre</li><li>Reviews</li><li>Contact</li></ul>
      </div>
      <div class="footer-col col-contact">
        <h5>Contact info</h5>
        <p class="contact-line">12 Maple Lane, Brookfield</p>
        <p class="contact-line">Northshire, AB1 2CD</p>
        <p class="contact-line" style="margin-top:6px">(0123) 456 789</p>
        <p class="contact-line">hello@tobymarlowe.com</p>
      </div>
      <div class="footer-col col-news">
        <h5>Newsletter signup</h5>
        <p>Get the latest news and offers straight to your inbox.</p>
        <div class="field"><span>Enter your email</span><b>Submit</b></div>
      </div>
      <div class="footer-col col-social">
        <h5>Social media</h5>
        <p>Connect with us on social media</p>
        <div class="social"><span></span><span></span><span></span><span></span><span></span></div>
      </div>
    </div>
  </footer>
  <div class="copyright">Copyright © 2015 Toby Marlowe. All Rights Reserved.</div>

</div>
</body>
</html>
```